Brell Stone Company Business Cards

Front and Back Business Card - logo and text setup - cool design. I need workable photoshop or illustrator files so I can setup each employee card with design that is created
Updates

Hi everyone, thank you for the great entries. Please no more white and blue cards - there are so many already - black and silver only now please. thanks!

Target Market(s)

Construction Industry - Facility Managers

Industry/Entity Type

Construction

Contact Information for Business Card

I really like contemporary simplistic looks - clean neat....not opposed to seeing some black backrounds

Requirements
Must have
• Logo/website address with design on front only - www.brellstone-example.com (logo attached)
• Back:
• Name/Title/Company Address/Phone/email address
Nice to have
• Cool design
Should not have
• Nothing gimmicky like Fire or Water - since we are a Fire Protection company - it has all been done

```html
<!DOCTYPE html>
<html lang="en">
<head>
<meta charset="utf-8">
<title>Brell Stone Company Business Cards</title>
<link rel="stylesheet" href="https://fonts.googleapis.com/css2?family=Josefin+Sans:wght@300;400;700&display=swap">
<style>
  :root {
    --black: #121314;
    --silver: #c3c5c9;
    --silver-light: #e4e5e7;
    --silver-dim: #8e9197;
    --backdrop: #e9eaec;
    --edge: #3a3b3d;
    --faint-silver: rgba(195, 197, 201, 0.07);
  }
  * { box-sizing: border-box; margin: 0; padding: 0; }
  html, body {
    width: 690px; height: 1200px; overflow: hidden;
    background: var(--backdrop);
    font-family: "Josefin Sans", sans-serif;
  }
  .sheet {
    width: 690px; height: 1200px;
    display: flex; flex-direction: column; align-items: center; justify-content: center;
    gap: 40px;
  }
  .card {
    position: relative;
    width: 640px; height: 366px;
    background: var(--black);
    border: 1px solid var(--edge);
    overflow: hidden;
  }
  .wordmark { display: flex; align-items: center; }
  .wordmark-square { background: var(--silver); flex: none; }
  .wordmark-name {
    font-weight: 700; color: var(--silver);
    letter-spacing: -0.5px; line-height: 1; white-space: nowrap;
  }
  /* front */
  .front .wordmark {
    position: absolute; left: 0; right: 0; top: 138px;
    justify-content: center; gap: 16px;
  }
  .front .wordmark-square { width: 22px; height: 22px; }
  .front .wordmark-name { font-size: 62px; }
  .front .rule {
    position: absolute; left: 0; right: 0; top: 324px;
    height: 2px; background: var(--silver-dim);
  }
  .front .site-pill {
    position: absolute; left: 50%; top: 309px; transform: translateX(-50%);
    background: var(--silver); color: var(--black);
    font-size: 17px; letter-spacing: 2px; font-weight: 400; line-height: 1;
    padding: 9px 18px 6px; border-radius: 16px; white-space: nowrap;
  }
  /* back */
  .back .decor-name {
    position: absolute; left: 570px; top: 80px;
    transform: translate(-50%, -50%) rotate(-55deg);
    font-weight: 700; font-size: 80px; color: var(--faint-silver);
    white-space: nowrap; line-height: 1;
  }
  .back .person {
    position: absolute; left: 0; right: 0; top: 50px; text-align: center;
  }
  .person-name {
    font-size: 30px; font-weight: 400; color: var(--silver-light); letter-spacing: 1.5px;
  }
  .person-title {
    font-size: 22px; font-weight: 300; color: var(--silver-dim); letter-spacing: 3px; margin-top: 4px;
  }
  .contact-list {
    position: absolute; left: 40px; top: 192px; list-style: none;
    color: var(--silver); font-size: 14px; letter-spacing: 1px; line-height: 21px;
  }
  .contact-item { display: flex; gap: 10px; margin-bottom: 6px; }
  .contact-icon { width: 14px; height: 14px; flex: none; margin-top: 2px; }
  .back .wordmark {
    position: absolute; right: 26px; bottom: 32px; gap: 10px;
  }
  .back .wordmark-name { font-size: 34px; }
  .back .wordmark-square { width: 12px; height: 12px; }
</style>
</head>
<body>
<main class="sheet">
  <section class="card front" aria-label="Card front">
    <div class="wordmark">
      <span class="wordmark-square"></span>
      <span class="wordmark-name">Brell Stone</span>
    </div>
    <div class="rule"></div>
    <div class="site-pill">www.brellstone-example.com</div>
  </section>

  <section class="card back" aria-label="Card back">
    <div class="decor-name" aria-hidden="true">Brell Stone</div>
    <div class="person">
      <div class="person-name">Dana Mirel Hawkins</div>
      <div class="person-title">President</div>
    </div>
    <ul class="contact-list">
      <li class="contact-item">
        <svg class="contact-icon" viewBox="0 0 14 14" aria-hidden="true"><circle cx="7" cy="7" r="6" fill="none" stroke="#c3c5c9" stroke-width="1.2"/><path d="M4.6 4.2l1.3-.3.6 1.5-.8.6a4 4 0 0 0 2.3 2.3l.6-.8 1.5.6-.3 1.3C7.3 9.6 4.4 6.7 4.6 4.2z" fill="#c3c5c9"/></svg>
        <span>T: (555) 010-4821<br>F: (555) 010-4822</span>
      </li>
      <li class="contact-item">
        <svg class="contact-icon" viewBox="0 0 14 14" aria-hidden="true"><circle cx="7" cy="7" r="6" fill="none" stroke="#c3c5c9" stroke-width="1.2"/><rect x="4" y="5" width="6" height="4.2" fill="none" stroke="#c3c5c9" stroke-width="1"/><path d="M4 5l3 2.3L10 5" fill="none" stroke="#c3c5c9" stroke-width="1"/></svg>
        <span>dana@brellstone-example.com</span>
      </li>
      <li class="contact-item">
        <svg class="contact-icon" viewBox="0 0 14 14" aria-hidden="true"><circle cx="7" cy="7" r="6" fill="none" stroke="#c3c5c9" stroke-width="1.2"/><path d="M1 7h12M7 1c-2 2-2 10 0 12M7 1c2 2 2 10 0 12" fill="none" stroke="#c3c5c9" stroke-width="0.9"/></svg>
        <span>www.brellstone-example.com</span>
      </li>
      <li class="contact-item">
        <svg class="contact-icon" viewBox="0 0 14 14" aria-hidden="true"><path d="M7 13s-4.5-4.5-4.5-7.5a4.5 4.5 0 0 1 9 0C11.5 8.5 7 13 7 13z" fill="none" stroke="#c3c5c9" stroke-width="1.2"/><circle cx="7" cy="5.5" r="1.6" fill="#c3c5c9"/></svg>
        <span>48 Harbor Point Road<br>Lakeview, NY 10999</span>
      </li>
    </ul>
    <div class="wordmark">
      <span class="wordmark-square"></span>
      <span class="wordmark-name">Brell Stone</span>
    </div>
  </section>
</main>
</body>
</html>
```